Business Card Design

We provide services doing multiple jobs in the construction industry.Please note: The company name needs to be ROCK SOLID BUILDING SERVICESAttached logo was an example of what we wanted. Can you change up the colors?

Industry/Entity Type

Construction

Contact Information for Business Card

ROCK SOLID BUILDING SERVICES5401 HUDSON BEND RDAUSTIN, TX 78734(512)243-6854ROCKSOLIDBUILDINGSERVICES@GMAIL.COM

```html
<!DOCTYPE html>
<html lang="en">
<head>
<meta charset="utf-8">
<title>Pearlwood Framing Works – Business Card</title>
<link rel="stylesheet" href="https://fonts.googleapis.com/css2?family=Alegreya+Sans:wght@400;500;700;800&display=swap">
<style>
  :root {
    --backdrop: #e9e6e1;
    --card: #ffffff;
    --ink: #111111;
    --navy: #23236b;
    --rule: #2e3a8c;
    --accent: #3fa4c4;
  }
  * { box-sizing: border-box; margin: 0; padding: 0; }
  html, body {
    width: 1200px;
    height: 849px;
    overflow: hidden;
    background: var(--backdrop);
    font-family: "Alegreya Sans", sans-serif;
  }
  .card {
    position: absolute;
    left: 150px;
    top: 168px;
    width: 900px;
    height: 514px;
    background: var(--card);
    box-shadow: 0 6px 24px rgba(0,0,0,0.12);
  }
  .brand-mark {
    position: absolute;
    top: 78px;
    left: 0;
    right: 0;
    display: flex;
    justify-content: center;
    align-items: center;
    gap: 14px;
  }
  .brand-mark__square {
    width: 34px;
    height: 34px;
    background: var(--accent);
  }
  .brand-mark__name {
    font-weight: 800;
    font-size: 30px;
    letter-spacing: 1px;
    color: var(--navy);
  }
  .name-rule {
    position: absolute;
    top: 210px;
    left: 0;
    right: 0;
    display: flex;
    align-items: center;
  }
  .name-rule__line {
    flex: 1;
    height: 4px;
    background: var(--rule);
  }
  .company-name {
    padding: 0 10px;
    font-weight: 800;
    font-size: 40px;
    letter-spacing: 1px;
    color: var(--ink);
    white-space: nowrap;
  }
  .contact {
    position: absolute;
    top: 290px;
    left: 0;
    right: 0;
    text-align: center;
    list-style: none;
    color: var(--navy);
    font-weight: 500;
    font-size: 30px;
    line-height: 58px;
  }
</style>
</head>
<body>
  <section class="card">
    <div class="brand-mark">
      <span class="brand-mark__square"></span>
      <span class="brand-mark__name">PEARLWOOD FRAMING WORKS</span>
    </div>
    <div class="name-rule">
      <span class="name-rule__line"></span>
      <h1 class="company-name">PEARLWOOD FRAMING WORKS</h1>
      <span class="name-rule__line"></span>
    </div>
    <ul class="contact">
      <li class="contact__phone">(512)555-0193</li>
      <li class="contact__email">Pearlwoodframingworks@mailnest.example</li>
      <li class="contact__address">7732 Fernglen Pass LN Austin, TX 78734</li>
    </ul>
  </section>
</body>
</html>
```